Business Card Design Project : Ridgeline Press

In preparation for market launch, Tamarind's Ridgeline Press require the development of a business card. Ridgeline Press is a Community online publishing web portal. We provide the the city of Whistler located in B.C. (Canada) business directories, News, Classified ads, News, Events and blogs etc.

The main focus of the brand is to help local businesses to corporate with their online advertisement and marketing. Meeting our clients face to face is a must (B2B).

Target Market(s)

The target market is B2B customers. Business Owners to Marketing, advertising Managers

Industry/Entity Type

Business

Requirements
Must have
• - The business card will be two sided.
the BACK side will have our logo which consist of (icon, url,slogan) submited. The logo will be middle and centred.

The FRONT side should have company details:

Company Legal Name: TAMARIND RIDGELINE MEDIA

Owen Farsk
Director of Sales & Marketing

www.tamarindridgeline.biz
owen@tamarindridgeline.biz

Phone: 604 317 8842
#2714 - 582 E. Halvern St.
Vancouver, B.C. V7K2R4 Canada
Nice to have
• - For the "FRONT" side of our business card. You can separate or re-arrange with our logo components (icon, logo,slogan). It does not have to be together.

Also our company legal name is rather long so arrange or organize the name in a way to make it shorter. Your experience and creativity will have to come in play.
Should not have
• should not have other colors beside logo color and black text (2 colors). Also nothing Three dimensional

```html
<!DOCTYPE html>
<html lang="en">
<head>
<meta charset="utf-8">
<title>Ridgeline Press – Business Card</title>
<link rel="stylesheet" href="https://fonts.googleapis.com/css2?family=Open+Sans:wght@400;600;700&display=swap">
<style>
  :root {
    --brand-blue: #2a7cc7;
    --ink: #111111;
    --paper: #ffffff;
    --stage: #e6e7e9;
    --paper-tint: #f4f6fa;
  }
  * { box-sizing: border-box; margin: 0; padding: 0; }
  html, body {
    width: 1200px; height: 900px; overflow: hidden;
    background: var(--stage);
    font-family: "Open Sans", Arial, sans-serif;
  }
  .stage {
    position: relative; width: 1200px; height: 900px;
    display: flex; align-items: center; justify-content: center; gap: 40px;
  }
  .card {
    position: relative; width: 525px; height: 300px;
    background: var(--paper-tint);
    box-shadow: 0 2px 8px rgba(0,0,0,0.12);
    overflow: hidden;
  }

  /* Back side */
  .card-back {
    display: flex; flex-direction: column; align-items: center; justify-content: center;
  }
  .brand-mark {
    display: flex; align-items: center; gap: 10px;
    color: var(--brand-blue); font-weight: 700; font-size: 30px;
    line-height: 1.2; margin-bottom: 10px;
  }
  .brand-mark .dot {
    width: 16px; height: 16px; border-radius: 50%; background: var(--brand-blue);
  }
  .url {
    color: var(--ink); font-weight: 700; font-size: 27px; letter-spacing: -0.5px; line-height: 1.25;
  }
  .slogan {
    color: var(--brand-blue); font-size: 17px; line-height: 1.3;
  }
  .card-back .slogan { align-self: center; margin-left: 70px; }

  /* Front side */
  .band { position: absolute; inset: 0; }
  .company {
    position: absolute; top: 12px; right: 70px;
    color: var(--brand-blue); font-weight: 700; font-size: 21px; line-height: 1.3;
  }
  .contact {
    position: absolute; top: 60px; left: 24px;
    color: var(--paper); font-size: 11.5px; line-height: 1.45;
  }
  .contact .person { color: var(--ink); font-weight: 700; font-size: 15px; line-height: 1.2; }
  .contact .role { margin-bottom: 3px; }
  .contact .line { display: flex; align-items: center; gap: 6px; }
  .contact .line svg { width: 10px; height: 10px; flex: none; }
  .contact .address { margin-top: 2px; }
  .front-sign {
    position: absolute; right: 22px; bottom: 14px; text-align: right;
  }
  .front-sign .brand-mark { justify-content: flex-end; font-size: 20px; margin-bottom: 2px; }
  .front-sign .brand-mark .dot { width: 12px; height: 12px; }
  .front-sign .url { font-size: 22px; }
  .front-sign .slogan { font-size: 14px; }
</style>
</head>
<body>
<main class="stage">

  <section class="card card-back" aria-label="Business card, back side">
    <div class="brand-mark"><span class="dot"></span><span>Ridgeline Press</span></div>
    <div class="url">www.tamarindridgeline.biz</div>
    <div class="slogan">Your information gateway</div>
  </section>

  <section class="card card-front" aria-label="Business card, front side">
    <svg class="band" viewBox="0 0 525 300" aria-hidden="true">
      <polygon points="0,50 390,50 455,194 0,194" fill="var(--brand-blue)"/>
    </svg>
    <div class="company">Tamarind Ridgeline Press</div>
    <div class="contact">
      <div class="person">Owen Farsk</div>
      <div class="role">Director of Sales &amp; Marketing</div>
      <div class="line">
        <svg viewBox="0 0 10 10"><rect x="2.5" y="0.5" width="5" height="9" rx="1" fill="none" stroke="currentColor"/></svg>
        <span>604 317 8842</span>
      </div>
      <div class="line">
        <svg viewBox="0 0 10 10"><rect x="0.5" y="2" width="9" height="6" fill="none" stroke="currentColor"/><path d="M0.5 2 L5 5.5 L9.5 2" fill="none" stroke="currentColor"/></svg>
        <span>owen@tamarindridgeline.biz</span>
      </div>
      <div class="line">
        <svg viewBox="0 0 10 10"><circle cx="5" cy="5" r="4.3" fill="none" stroke="currentColor"/><ellipse cx="5" cy="5" rx="1.8" ry="4.3" fill="none" stroke="currentColor"/></svg>
        <span>www.tamarindridgeline.biz</span>
      </div>
      <div class="address">#2714 - 582 E. Halvern St.<br>Vancouver, B.C. V7K2R4 Canada</div>
    </div>
    <div class="front-sign">
      <div class="brand-mark"><span>Ridgeline Press</span><span class="dot"></span></div>
      <div class="url">www.tamarindridgeline.biz</div>
      <div class="slogan">Your information gateway</div>
    </div>
  </section>

</main>
</body>
</html>
```